Double Sided Flyer for 3D printing services company

We need a nice balanced flyer for our corporate handout. The attached is for concept only and not the final design. We think the attached examples have elements that balance nicely but the graphics are not good. We are attaching the logo from the corporate office for our new logo. We will add the company information after the final design is selected for web address, phone, mailing etc. Please leave room for that information in the design. Please ask any questions prior to submission. Our main focus is printing RUBBER 3D Parts and not plastic parts. The images selected should be focused on that. We also need to ensure the images are approved for use in a corporate flyer for content.

```html
<!DOCTYPE html>
<html lang="en">
<head>
<meta charset="UTF-8">
<title>Corvane – 3D Rubber Parts Flyer, Front and Back</title>
<link href="https://fonts.googleapis.com/css2?family=Montserrat:wght@400;500;600;700;800&display=swap" rel="stylesheet">
<style>
  :root {
    --orange: #e8692a;
    --ink: #2a2a2c;
    --text: #3a3a3c;
    --paper: #ffffff;
    --footer: #dedede;
    --backdrop: #9a9a9a;
    --steel-light: #8aa6c2;
    --steel-dark: #2c445e;
    --icon-ring: #c9c9c9;
    --icon-fill: #f1f1f1;
  }
  * { margin: 0; padding: 0; box-sizing: border-box; }
  html, body { width: 822px; height: 1200px; overflow: hidden; background: var(--backdrop); }
  body { font-family: "Montserrat", sans-serif; color: var(--text); position: relative; }

  .sheet { position: absolute; top: 319px; width: 398px; height: 562px; overflow: hidden; box-shadow: 0 3px 10px rgba(0,0,0,.25); }
  .sheet-front { left: 8px; }
  .sheet-back { left: 416px; }
  .page { position: absolute; left: 0; top: 0; width: 675px; height: 953px; background: var(--paper);
    transform: scale(0.5896); transform-origin: 0 0; overflow: hidden; }

  /* shared pieces */
  .brand { position: absolute; display: flex; align-items: center; gap: 12px; }
  .brand-mark { width: 54px; height: 54px; border-radius: 50%; background: var(--orange); flex: none; }
  .brand-name { font-weight: 800; font-size: 44px; line-height: 1; color: var(--ink); letter-spacing: 1px; }
  .brand-tagline { font-weight: 500; font-size: 12.5px; letter-spacing: 2.2px; color: var(--ink); margin-top: 4px; }
  .rule { position: absolute; height: 3px; background: var(--orange); }
  .tag { position: absolute; height: 26px; padding: 0 15px; background: var(--orange); color: #fff;
    font-weight: 700; font-size: 13px; letter-spacing: 1.3px; display: flex; align-items: center; white-space: nowrap; }
  .photo { position: absolute; }

  .footer-band { position: absolute; left: 0; top: 866px; width: 100%; height: 87px; background: var(--footer); }
  .contact-tag { left: 25px; top: 852px; z-index: 2; }
  .contact-row { position: absolute; left: 25px; right: 24px; top: 905px; display: flex; align-items: center; justify-content: space-between; }
  .contact-item { display: flex; align-items: center; gap: 10px; font-size: 13.5px; color: var(--ink); letter-spacing: .6px; white-space: nowrap; }
  .contact-item b { font-weight: 700; }
  .contact-divider { width: 1.5px; height: 24px; background: var(--ink); }

  /* front */
  .front-brand { left: 25px; top: 27px; }
  .front-header-rule { left: 0; top: 113px; width: 100%; }
  .hero-photo { left: 0; top: 116px; width: 675px; height: 412px;
    background: radial-gradient(ellipse at 45% 60%, var(--steel-light), var(--steel-dark) 85%); }
  .inset-photo { left: 350px; top: 369px; width: 300px; height: 231px; border: 3px solid var(--orange);
    box-shadow: 0 3px 10px rgba(0,0,0,.35);
    background: linear-gradient(135deg, #d9d9d9 0%, #4a4a4a 40%, #222 60%, #c23a3a 80%, #e8e8e8 100%); }

  .headline { position: absolute; left: 25px; top: 548px; display: flex; align-items: flex-end; gap: 8px; }
  .headline-3d { font-weight: 700; font-size: 92px; line-height: .8; color: var(--orange); letter-spacing: -4px; }
  .headline-words { display: flex; flex-direction: column; color: var(--ink); font-weight: 700; }
  .headline-rubber { font-size: 29px; line-height: 1; display: flex; align-items: center; gap: 8px; }
  .headline-rubber::after { content: ""; width: 30px; height: 2.5px; background: var(--orange); }
  .headline-parts { font-size: 49px; line-height: .9; }
  .headline-rule { left: 25px; top: 628px; width: 300px; }

  .tag-provide { left: 25px; top: 662px; }
  .tag-whatwedo { left: 350px; top: 630px; }

  .provide-list { position: absolute; left: 25px; top: 700px; list-style: none; }
  .provide-item { display: flex; align-items: center; gap: 10px; font-weight: 600; font-size: 11px; line-height: 1.2;
    color: var(--ink); letter-spacing: .4px; height: 24px; margin-bottom: 9px; }
  .provide-item svg { flex: none; }

  .services { position: absolute; left: 350px; top: 670px; width: 300px; list-style: none; }
  .service { position: relative; padding-left: 12px; font-size: 10.6px; line-height: 1.22; color: var(--text); margin-bottom: 13px; }
  .service::before { content: ""; position: absolute; left: 0; top: 4.5px; width: 5px; height: 5px; border-radius: 50%; background: var(--orange); }

  /* back */
  .back-photo { left: 0; top: 0; width: 675px; height: 246px;
    background: radial-gradient(ellipse at 55% 50%, #e6ecf4 0%, #9fb0c8 40%, #46556e 80%, #2d384a 100%); }
  .back-photo-rule { left: 0; top: 246px; width: 100%; }

  .intro-title { position: absolute; left: 25px; top: 268px; font-weight: 700; font-size: 21px; line-height: 1.1; color: var(--ink); letter-spacing: .8px; }
  .intro-title .accent { color: var(--orange); }
  .intro-sub { position: absolute; left: 25px; top: 352px; font-weight: 700; font-size: 13px; letter-spacing: .9px; color: var(--ink); }
  .lead { position: absolute; left: 25px; top: 388px; font-weight: 600; font-size: 15px; color: var(--orange); letter-spacing: .5px; }
  .lead-body { position: absolute; left: 25px; top: 412px; font-size: 10.6px; line-height: 1.25; color: var(--text); }
  .tag-easy { left: 25px; top: 464px; }

  .steps { position: absolute; left: 25px; top: 508px; list-style: none; width: 300px; }
  .step { display: flex; align-items: center; gap: 10px; font-weight: 600; font-size: 10.6px; line-height: 1.2; color: var(--ink); letter-spacing: .3px; height: 24px; margin-bottom: 9px; }
  .step-num { flex: none; width: 23px; height: 23px; border-radius: 50%; background: var(--orange); color: #fff;
    font-weight: 700; font-size: 11px; display: flex; align-items: center; justify-content: center; }
  .steps-rule { left: 25px; top: 614px; width: 300px; height: 2px; }

  .callout { position: absolute; left: 25px; top: 626px; width: 300px; font-weight: 500; font-size: 15.5px; line-height: 1.25; color: var(--orange); letter-spacing: .5px; }
  .quote-rule { position: absolute; left: 25px; top: 710px; width: 300px; height: 1px; background: var(--orange); }
  .quote-mark { position: absolute; left: 25px; top: 714px; }
  .quote-text { position: absolute; left: 25px; top: 736px; width: 300px; font-size: 10.6px; line-height: 1.25; color: var(--text); }
  .quote-by { position: absolute; left: 25px; top: 820px; width: 300px; display: flex; align-items: center; gap: 6px; }
  .quote-by::before { content: ""; flex: 1; height: 1px; background: var(--orange); }
  .quote-by span { font-weight: 600; font-size: 10.6px; color: var(--orange); letter-spacing: .4px; white-space: nowrap; }

  .back-brand { left: 350px; top: 272px; }
  .back-brand .brand-name { font-size: 41px; }
  .back-brand .brand-tagline { font-size: 11.5px; letter-spacing: 2px; }
  .benefits-title { position: absolute; left: 350px; top: 354px; font-weight: 700; font-size: 21px; line-height: 1.1; color: var(--ink); letter-spacing: .8px; }
  .benefits-title .accent { color: var(--orange); }
  .benefits-rule { left: 350px; top: 412px; width: 300px; height: 2px; }

  .benefit-card { position: absolute; left: 350px; width: 300px; height: 70px; border: 2px solid var(--orange); border-radius: 10px;
    display: flex; align-items: center; gap: 8px; padding: 0 10px 0 0; background: var(--paper); }
  .benefit-card.icon-right { flex-direction: row-reverse; padding: 0 0 0 10px; }
  .benefit-icon { flex: none; width: 50px; height: 50px; border-radius: 50%; border: 2px solid var(--icon-ring); background: var(--icon-fill);
    display: flex; align-items: center; justify-content: center; margin-left: -2px; }
  .icon-right .benefit-icon { margin-left: 0; margin-right: 6px; }
  .benefit-pointer { flex: none; width: 0; height: 0; border-top: 5px solid transparent; border-bottom: 5px solid transparent; border-left: 6px solid var(--orange); }
  .icon-right .benefit-pointer { border-left: 0; border-right: 6px solid var(--orange); }
  .benefit-copy { flex: 1; }
  .benefit-title { font-weight: 700; font-size: 10.6px; color: var(--orange); letter-spacing: .4px; margin-bottom: 4px; }
  .benefit-body { font-size: 8.6px; line-height: 1.2; color: var(--text); }
  .card-1 { top: 436px; } .card-2 { top: 517px; } .card-3 { top: 598px; } .card-4 { top: 679px; } .card-5 { top: 760px; }
</style>
</head>
<body>

<section class="sheet sheet-front">
  <div class="page">
    <header>
      <div class="brand front-brand">
        <span class="brand-mark"></span>
        <div>
          <div class="brand-name">CORVANE</div>
          <div class="brand-tagline">SEALS·GASKETS·HOSES</div>
        </div>
      </div>
      <div class="rule front-header-rule"></div>
    </header>

    <div class="photo hero-photo" role="img" aria-label="3D printer nozzle printing a black lattice rubber part, cool blue tones"></div>
    <div class="photo inset-photo" role="img" aria-label="Assorted black and red rubber seals, gaskets, bellows and O-rings"></div>

    <h1 class="headline">
      <span class="headline-3d">3D</span>
      <span class="headline-words">
        <span class="headline-rubber">RUBBER</span>
        <span class="headline-parts">PARTS</span>
      </span>
    </h1>
    <div class="rule headline-rule"></div>

    <div class="tag tag-provide">WE PROVIDE</div>
    <ul class="provide-list">
      <li class="provide-item">
        <svg width="24" height="24" viewBox="0 0 30 30"><circle cx="15" cy="15" r="15" fill="#e8692a"/><path d="M10 8h10M10 22h10M11 8c0 5 8 5 8 7s-8 2-8 7M19 8c0 5-8 5-8 7s8 2 8 7" stroke="#fff" stroke-width="1.6" fill="none"/></svg>
        <span>Reduce time to Market from<br>Weeks to Hours</span>
      </li>
      <li class="provide-item">
        <svg width="24" height="24" viewBox="0 0 30 30"><circle cx="15" cy="15" r="15" fill="#e8692a"/><rect x="8" y="8" width="14" height="14" rx="2" stroke="#fff" stroke-width="1.6" fill="none"/><path d="M11 15l3 3 5-6" stroke="#fff" stroke-width="1.8" fill="none"/></svg>
        <span>Eliminate Costly Design Errors</span>
      </li>
      <li class="provide-item">
        <svg width="24" height="24" viewBox="0 0 30 30"><circle cx="15" cy="15" r="15" fill="#e8692a"/><circle cx="15" cy="16" r="7" stroke="#fff" stroke-width="1.6" fill="none"/><path d="M15 16V12M13 7h4" stroke="#fff" stroke-width="1.6"/></svg>
        <span>Faster time to Market</span>
      </li>
      <li class="provide-item">
        <svg width="24" height="24" viewBox="0 0 30 30"><circle cx="15" cy="15" r="15" fill="#e8692a"/><path d="M15 8v14M18.5 11.5c-1-1.5-7-1.5-7 1s7 1.5 7 4-6 2.5-7 1" stroke="#fff" stroke-width="1.7" fill="none"/></svg>
        <span>Reduced R and D Budgets</span>
      </li>
    </ul>

    <div class="tag tag-whatwedo">WHAT WE DO</div>
    <ul class="services">
      <li class="service">The focus of our 3D printing service is on Rubber Parts for the medical and Military fields primarily. But overall its about rubber parts only and not plastic parts.</li>
      <li class="service">We take this from prototype to production quickly. Interim steps are to create cast molds for working short run parts OR injection molds for high volume parts. The return is quick and our turnaround is fast. Taking design from months to weeks. Prototypes from weeks to hours.</li>
    </ul>

    <footer>
      <div class="tag contact-tag">CONTACT US</div>
      <div class="footer-band"></div>
      <div class="contact-row">
        <div class="contact-item">
          <svg width="22" height="22" viewBox="0 0 28 28"><rect width="28" height="28" fill="#e8692a"/><circle cx="14" cy="14" r="8" stroke="#fff" stroke-width="1.5" fill="none"/><ellipse cx="14" cy="14" rx="3.5" ry="8" stroke="#fff" stroke-width="1.3" fill="none"/><path d="M6 14h16" stroke="#fff" stroke-width="1.3"/></svg>
          <span>www.<b>corvane</b>.com</span>
        </div>
        <span class="contact-divider"></span>
        <div class="contact-item">
          <svg width="22" height="22" viewBox="0 0 28 28"><rect width="28" height="28" fill="#e8692a"/><path d="M9 7l3 0 1.5 4-2 1.5c1 2 2.5 3.5 4.5 4.5l1.5-2 4 1.5v3c0 1-1 1.5-2 1.5C12 21 7 16 7 9c0-1 .8-2 2-2z" stroke="#fff" stroke-width="1.4" fill="none"/></svg>
          <b>555-014-2087</b>
        </div>
        <span class="contact-divider"></span>
        <div class="contact-item">
          <svg width="22" height="22" viewBox="0 0 28 28"><rect width="28" height="28" fill="#e8692a"/><rect x="6" y="8.5" width="16" height="11" stroke="#fff" stroke-width="1.4" fill="none"/><path d="M6 8.5l8 6 8-6" stroke="#fff" stroke-width="1.4" fill="none"/></svg>
          <span>info@<b>corvane</b>.com</span>
        </div>
      </div>
    </footer>
  </div>
</section>

<section class="sheet sheet-back">
  <div class="page">
    <div class="photo back-photo" role="img" aria-label="Black and white 3D printed rubber prototypes on a printer bed, cool blue-grey tones"></div>
    <div class="rule back-photo-rule"></div>

    <h2 class="intro-title">REDEFINE<br>YOUR INDUTRY WITH<br><span class="accent">3D PRINTING</span></h2>
    <p class="intro-sub">GASKETS &amp; RUBBER PARTS</p>
    <p class="lead">Need quality parts?</p>
    <p class="lead-body">Lety us print your custom one-off<br>or production pieces.</p>

    <div class="tag tag-easy">EASY AS 1*2*3</div>
    <ol class="steps">
      <li class="step"><span class="step-num">1</span><span>Send us your Rubber part design file</span></li>
      <li class="step"><span class="step-num">2</span><span>Receive your Estimate within 24 hours</span></li>
      <li class="step"><span class="step-num">3</span><span>Receive your prototype sample<br>within 10 days</span></li>
    </ol>
    <div class="rule steps-rule"></div>

    <p class="callout">Confirm fitment and function before losing time and money on costly molds *</p>

    <div class="quote-rule"></div>
    <svg class="quote-mark" width="26" height="16" viewBox="0 0 26 16"><path d="M10 2C5 2 2 5 2 9s2 5 4.5 5S10 12 10 10 8.5 7 6.5 7C7 5 8.5 4 10 4zM23 2c-5 0-8 3-8 7s2 5 4.5 5 3.5-2 3.5-4-1.5-3-3.5-3c.5-2 2-3 3.5-3z" fill="#e8692a"/></svg>
    <p class="quote-text">The 3d printer was one of the best investments that Halvern-Brooks has made in years. Being a custom manufacturer of urethane products, we now have the capability to produce masters for our customers in house and it has allowed us to service new industries.</p>
    <p class="quote-by"><span>Marcus L. - Engineering Manager</span></p>

    <div class="brand back-brand">
      <span class="brand-mark"></span>
      <div>
        <div class="brand-name">CORVANE</div>
        <div class="brand-tagline">SEALS·GASKETS·HOSES</div>
      </div>
    </div>
    <h2 class="benefits-title"><span class="accent">BENEFITS</span> OF 3D<br>PRINTING</h2>
    <div class="rule benefits-rule"></div>

    <div class="benefit-card card-1">
      <span class="benefit-icon"><svg width="26" height="26" viewBox="0 0 26 26"><path d="M4 18a9 9 0 1 1 18 0" stroke="#444" stroke-width="1.6" fill="none"/><path d="M13 18l5-6" stroke="#444" stroke-width="1.6"/><circle cx="13" cy="18" r="1.6" fill="#444"/></svg></span>
      <span class="benefit-pointer"></span>
      <div class="benefit-copy">
        <p class="benefit-title">Speed Time to Market</p>
        <p class="benefit-body">Compress design cycles by 3D printing multiple prototypes on demand, right in your office.</p>
      </div>
    </div>
    <div class="benefit-card icon-right card-2">
      <span class="benefit-icon"><svg width="26" height="26" viewBox="0 0 26 26"><circle cx="13" cy="13" r="8" stroke="#444" stroke-width="1.6" fill="none"/><path d="M15.5 10c-.7-1-5-1-5 .8s5 1 5 3-4.3 1.8-5 .8M13 7.5v11" stroke="#444" stroke-width="1.4" fill="none"/></svg></span>
      <span class="benefit-pointer"></span>
      <div class="benefit-copy">
        <p class="benefit-title">Reduce Development Costs</p>
        <p class="benefit-body">Cut traditional prototyping and tooling costs. Identify design errors earlier and reduce travel to production facilities.</p>
      </div>
    </div>
    <div class="benefit-card card-3">
      <span class="benefit-icon"><svg width="26" height="26" viewBox="0 0 26 26"><path d="M6 13l4 4 10-10" stroke="#444" stroke-width="1.8" fill="none"/><rect x="3" y="3" width="20" height="20" rx="3" stroke="#444" stroke-width="1.4" fill="none"/></svg></span>
      <span class="benefit-pointer"></span>
      <div class="benefit-copy">
        <p class="benefit-title">Win Business</p>
        <p class="benefit-body">Bring realistic 3D models to prospective accounts, sponsors and focus groups.</p>
      </div>
    </div>
    <div class="benefit-card icon-right card-4">
      <span class="benefit-icon"><svg width="26" height="26" viewBox="0 0 26 26"><path d="M13 4a6.5 6.5 0 0 0-4 11.6V18h8v-2.4A6.5 6.5 0 0 0 13 4z" stroke="#444" stroke-width="1.5" fill="none"/><path d="M10 21h6" stroke="#444" stroke-width="1.5"/></svg></span>
      <span class="benefit-pointer"></span>
      <div class="benefit-copy">
        <p class="benefit-title">Increase Innovation</p>
        <p class="benefit-body">Print prototypes in hours, obtain feedback, refine designs and repeat the cycle until designs are perfect.</p>
      </div>
    </div>
    <div class="benefit-card card-5">
      <span class="benefit-icon"><svg width="26" height="26" viewBox="0 0 26 26"><circle cx="13" cy="13" r="4" stroke="#444" stroke-width="1.5" fill="none"/><path d="M13 3v4M13 19v4M3 13h4M19 13h4M6 6l2.8 2.8M17.2 17.2L20 20M6 20l2.8-2.8M17.2 8.8L20 6" stroke="#444" stroke-width="1.5"/></svg></span>
      <span class="benefit-pointer"></span>
      <div class="benefit-copy">
        <p class="benefit-title">Personalise Products</p>
        <p class="benefit-body">Personalise merchandise such as pens and other items at conventions etc. This can increase mindshare with potential clients.</p>
      </div>
    </div>

    <footer>
      <div class="tag contact-tag">CONTACT US</div>
      <div class="footer-band"></div>
      <div class="contact-row">
        <div class="contact-item">
          <svg width="22" height="22" viewBox="0 0 28 28"><rect width="28" height="28" fill="#e8692a"/><circle cx="14" cy="14" r="8" stroke="#fff" stroke-width="1.5" fill="none"/><ellipse cx="14" cy="14" rx="3.5" ry="8" stroke="#fff" stroke-width="1.3" fill="none"/><path d="M6 14h16" stroke="#fff" stroke-width="1.3"/></svg>
          <span>www.<b>corvane</b>.com</span>
        </div>
        <span class="contact-divider"></span>
        <div class="contact-item">
          <svg width="22" height="22" viewBox="0 0 28 28"><rect width="28" height="28" fill="#e8692a"/><path d="M9 7l3 0 1.5 4-2 1.5c1 2 2.5 3.5 4.5 4.5l1.5-2 4 1.5v3c0 1-1 1.5-2 1.5C12 21 7 16 7 9c0-1 .8-2 2-2z" stroke="#fff" stroke-width="1.4" fill="none"/></svg>
          <b>555-014-2087</b>
        </div>
        <span class="contact-divider"></span>
        <div class="contact-item">
          <svg width="22" height="22" viewBox="0 0 28 28"><rect width="28" height="28" fill="#e8692a"/><rect x="6" y="8.5" width="16" height="11" stroke="#fff" stroke-width="1.4" fill="none"/><path d="M6 8.5l8 6 8-6" stroke="#fff" stroke-width="1.4" fill="none"/></svg>
          <span>info@<b>corvane</b>.com</span>
        </div>
      </div>
    </footer>
  </div>
</section>

</body>
</html>
```